Vernac Law Business cards and stationary design project

We are looking for a stationary design for business cards (double sided), 8x10, 5x7, and legal and standard envelopes.

We would like the design to match the logo that we have already.
Color palate preferred is Teal, White, grey and any others that will look good for a professional law firm.

We would like this statement: "RELATIONSHIPS. RESPECT. RESULT" to be on the back of the business cards and maybe on the stationary if it looks good.

Please see link to website for more information: www.vernac-law.example

Target Market(s)

Potential clients that need Attorney services.

Industry/Entity Type

Law Firm

Contact Information for Business Card

We would like the front and back to be two different colors. Current business cards are teal front, grey back and are a vertical design. We are open to options with colors.

Font styles to use
Serif

Colors
33a6d7
33b8a4
b9b9b9
5c5c5c

Requirements
Must have
• Logo supplied needs to go on the card and stationary.
• Match website color palate, www.vernac-law.example
• Be professional and not too wordy.
• Criminal Law, Civil Litigation, Personal Injury, Restraining Orders need to be on the card.
Nice to have
• RELATIONSHIPS. RESPECT. RESULTS. on the back of the card.
Should not have
• Not be too busy/wordy or too flashy.

```html
<!DOCTYPE html>
<html lang="en">
<head>
<meta charset="utf-8">
<title>Vernac Law – Envelope Stationery</title>
<link href="https://fonts.googleapis.com/css2?family=Lato:wght@400&display=swap" rel="stylesheet">
<style>
  :root {
    --backdrop: #c6c6c6;
    --paper: #e8e8e8;
    --teal: #1f7a86;
    --charcoal: #525252;
    --white: #ffffff;
  }
  * { box-sizing: border-box; margin: 0; padding: 0; }
  html, body { width: 1200px; height: 910px; overflow: hidden; }
  body { background: var(--backdrop); position: relative; font-family: "Lato", sans-serif; }

  .envelope {
    position: absolute;
    left: 261px;
    width: 745px;
    height: 320px;
    background: var(--paper);
  }
  .envelope--front { top: 98px; }
  .envelope--back { top: 486px; }

  .brand {
    position: absolute;
    left: 42px;
    top: 38px;
    display: flex;
    align-items: center;
    gap: 14px;
  }
  .brand__mark {
    width: 70px;
    height: 70px;
    border-radius: 50%;
    background: var(--teal);
  }
  .brand__name {
    color: var(--teal);
    font-family: "Lato", sans-serif;
    font-weight: 400;
    font-size: 28px;
    line-height: 1;
  }

  .contact-band {
    position: absolute;
    left: 0;
    right: 0;
    top: 264px;
    height: 42px;
    border-top: 2px solid var(--teal);
    border-bottom: 2px solid var(--teal);
    padding: 2px 0;
  }
  .contact-band__inner {
    height: 100%;
    background: var(--charcoal);
    display: flex;
    align-items: center;
    justify-content: center;
    gap: 6px;
    color: var(--white);
    font-size: 11.5px;
    white-space: nowrap;
  }
  .contact-item { display: flex; align-items: center; gap: 4px; }
  .contact-item svg { width: 9px; height: 9px; fill: var(--teal); }
  .contact-sep { color: var(--teal); font-size: 10px; }

  .flap {
    position: absolute;
    left: 0;
    top: 0;
    width: 745px;
    height: 118px;
  }
  .flap__brand {
    position: absolute;
    left: 0;
    right: 0;
    top: 26px;
    display: flex;
    align-items: center;
    justify-content: center;
    gap: 12px;
  }
  .flap__mark {
    width: 60px;
    height: 60px;
    border-radius: 50%;
    background: var(--teal);
  }
  .flap__name {
    color: var(--teal);
    font-family: "Lato", sans-serif;
    font-weight: 400;
    font-size: 24px;
    line-height: 1;
  }
</style>
</head>
<body>

<section class="envelope envelope--front" aria-label="Envelope front">
  <div class="brand">
    <div class="brand__mark" role="img" aria-label="Firm logo mark"></div>
    <div class="brand__name">Vernac Law</div>
  </div>

  <div class="contact-band">
    <div class="contact-band__inner">
      <span class="contact-item">
        <svg viewBox="0 0 10 10" aria-hidden="true"><path d="M5 0a3.5 3.5 0 0 0-3.5 3.5C1.5 6 5 10 5 10s3.5-4 3.5-6.5A3.5 3.5 0 0 0 5 0zm0 5a1.5 1.5 0 1 1 0-3 1.5 1.5 0 0 1 0 3z"/></svg>
        480 Harbor View Ave. #210 , Seacliff Bay, CA 90000
      </span>
      <span class="contact-sep">|</span>
      <span class="contact-item">
        <svg viewBox="0 0 10 10" aria-hidden="true"><path d="M2 0l2 2.5-1 1.2a6 6 0 0 0 3.3 3.3l1.2-1L10 8 8.5 10C4 10 0 6 0 1.5z"/></svg>
        (555) 014-2290
      </span>
      <span class="contact-sep">|</span>
      <span class="contact-item">
        <svg viewBox="0 0 10 10" aria-hidden="true"><path d="M0 2h10v6H0zM0 2l5 3.5L10 2" stroke="#525252" stroke-width="0.8"/></svg>
        mara@vernac-law.example
      </span>
      <span class="contact-sep">|</span>
      <span class="contact-item">
        <svg viewBox="0 0 10 10" aria-hidden="true"><circle cx="5" cy="5" r="5"/></svg>
        www.vernac-law.example
      </span>
    </div>
  </div>
</section>

<section class="envelope envelope--back" aria-label="Envelope back">
  <svg class="flap" viewBox="0 0 745 118" aria-hidden="true">
    <path d="M0 0H745L729 102Q727 118 711 118H34Q18 118 16 102Z" fill="var(--charcoal)"/>
  </svg>
  <div class="flap__brand">
    <div class="flap__mark" role="img" aria-label="Firm logo mark"></div>
    <div class="flap__name">Vernac Law</div>
  </div>
</section>

</body>
</html>
```